Moravel Aesthetic Doctor

I require an elegant, luxurious looking business card for my aesthetic business. I am a doctor and that will set me aside from competitors. I am planning to provide home and spa based treatments to clients with high expectations. I have attached my logo.

```html
<!DOCTYPE html>
<html lang="en">
<head>
<meta charset="utf-8">
<title>Moravel Aesthetic Doctor – Business Card</title>
<link rel="stylesheet" href="https://fonts.googleapis.com/css2?family=Roboto:wght@300;400;700&display=swap">
<style>
  :root {
    --backdrop: #3b3b3d;
    --card-front: #1d1d1f;
    --card-back: #232427;
    --card-back-shape: #2b2c30;
    --silver: #b9bcc2;
    --silver-dim: #8d9096;
    --text-grey: #c4c6cb;
    --blue: #2c8fd6;
    --blue-light: #5cb4ec;
    --blue-deep: #1670b8;
    --strip-grey: #aeb3bb;
  }
  * { box-sizing: border-box; margin: 0; padding: 0; }
  html, body {
    width: 799px; height: 1200px; overflow: hidden;
    background: var(--backdrop);
    font-family: "Roboto", Arial, sans-serif;
  }
  .sheet {
    width: 799px; height: 1200px;
    display: flex; flex-direction: column; align-items: center; justify-content: space-around;
    padding: 70px 0;
  }
  .card {
    position: relative; width: 560px; height: 320px; border-radius: 6px; overflow: hidden;
    box-shadow: 0 14px 30px rgba(0,0,0,.45);
  }

  /* Front */
  .card--front { background: var(--card-front); display: flex; align-items: center; justify-content: center; }
  .front-mark { display: flex; align-items: center; gap: 16px; }
  .front-mark__dot { width: 46px; height: 46px; border: 2px solid var(--silver-dim); border-radius: 50%; }
  .front-mark__name { font-weight: 300; font-size: 40px; letter-spacing: 3px; color: var(--silver); }

  /* Back */
  .card--back { background: var(--card-back); }
  .back-shape {
    position: absolute; right: -60px; top: 70px; width: 260px; height: 280px;
    border-radius: 50% 40% 0 50%;
    background: radial-gradient(circle at 40% 40%, var(--card-back-shape), var(--card-back) 75%);
  }
  .brand { position: absolute; left: 34px; top: 30px; display: flex; align-items: center; gap: 14px; }
  .brand__dot { width: 62px; height: 62px; border: 2px solid var(--silver-dim); border-radius: 50%; }
  .brand__name { font-weight: 300; font-size: 31px; letter-spacing: 1.5px; color: var(--silver); }

  .doctor { position: absolute; left: 34px; top: 118px; color: var(--blue); line-height: 1.2; }
  .doctor__name { font-weight: 700; font-size: 17px; }
  .doctor__post { font-weight: 400; font-size: 10px; margin-left: 4px; }
  .doctor__diploma { font-size: 14px; font-weight: 400; }

  .social { position: absolute; left: 34px; top: 200px; display: flex; align-items: center; gap: 6px;
    color: var(--text-grey); font-size: 13px; }
  .social__dot { width: 15px; height: 15px; border-radius: 50%; background: var(--blue); }
  .social__label { margin-right: 4px; }

  .contact { position: absolute; left: 300px; top: 178px; list-style: none; color: var(--text-grey); font-size: 14px; }
  .contact li { display: flex; align-items: center; gap: 10px; height: 20px; }
  .contact svg { width: 13px; height: 13px; fill: var(--blue); flex: none; }

  .strip-grey { position: absolute; left: 0; bottom: 0; width: 100%; height: 46px;
    background: linear-gradient(var(--strip-grey), var(--strip-grey)) left top / 100% 12px no-repeat; }
  .band {
    position: absolute; right: 0; bottom: 0; width: 360px; height: 46px;
    border-top-left-radius: 22px;
    background: linear-gradient(90deg, var(--blue-deep), var(--blue-light) 45%, var(--blue));
    color: #fff; font-size: 14px; letter-spacing: .4px; text-transform: uppercase;
    display: flex; align-items: center; justify-content: flex-end; padding-right: 22px;
  }
</style>
</head>
<body>
<main class="sheet">
  <section class="card card--front" aria-label="Card front">
    <div class="front-mark">
      <span class="front-mark__dot"></span>
      <span class="front-mark__name">Moravel</span>
    </div>
  </section>

  <section class="card card--back" aria-label="Card back">
    <div class="back-shape"></div>
    <div class="brand">
      <span class="brand__dot"></span>
      <span class="brand__name">Moravel Aesthetic Doctor</span>
    </div>

    <div class="doctor">
      <p class="doctor__name">Dr Lena Varis<span class="doctor__post">MRCPCH MD</span></p>
      <p class="doctor__diploma">Australasian Diploma<br>of Aesthetic Medicine</p>
    </div>

    <div class="social">
      <span class="social__label">Follow us on:</span>
      <span class="social__dot"></span>
      <span class="social__dot"></span>
    </div>

    <ul class="contact">
      <li><svg viewBox="0 0 24 24"><path d="M6.6 10.8a15.1 15.1 0 0 0 6.6 6.6l2.2-2.2c.3-.3.7-.4 1-.2 1.1.4 2.3.6 3.6.6.6 0 1 .4 1 1V20c0 .6-.4 1-1 1A17 17 0 0 1 3 4c0-.6.4-1 1-1h3.5c.6 0 1 .4 1 1 0 1.3.2 2.5.6 3.6.1.3 0 .7-.2 1z"/></svg>0800 472 915</li>
      <li><svg viewBox="0 0 24 24"><path d="M2 5h20v14H2zm2 2v.5l8 5 8-5V7l-8 5z"/></svg>lena@moravel.co.nz</li>
      <li><svg viewBox="0 0 24 24"><path d="M12 2a10 10 0 1 0 0 20 10 10 0 0 0 0-20zm6.9 9h-3a15 15 0 0 0-1.4-6 8 8 0 0 1 4.4 6zM12 4c.9 1.3 1.7 3.9 1.9 7h-3.8C10.3 7.9 11.1 5.3 12 4zM9.5 5a15 15 0 0 0-1.4 6h-3a8 8 0 0 1 4.4-6zM5.1 13h3a15 15 0 0 0 1.4 6 8 8 0 0 1-4.4-6zM12 20c-.9-1.3-1.7-3.9-1.9-7h3.8c-.2 3.1-1 5.7-1.9 7zm2.5-1a15 15 0 0 0 1.4-6h3a8 8 0 0 1-4.4 6z"/></svg>www.moravel.co.nz</li>
    </ul>

    <div class="strip-grey"></div>
    <div class="band">Home and spa based treatments</div>
  </section>
</main>
</body>
</html>
```